Theatre Company needs a Poster design for a world premiere of "The Lantern" Play.

We are premiering a play that celebrates community in rural and regional Australia . We need a poster for A3 and A5 size and an image that can be used in our email correspondence/webpage.

Attached is some ideas the producing theatre committee has come up with, a river runs through the town itself.

Town

```html
<!DOCTYPE html>
<html lang="en">
<head>
<meta charset="utf-8">
<title>The Lantern — Poster</title>
<link rel="stylesheet" href="https://fonts.googleapis.com/css2?family=Playfair+Display:wght@400;500&family=Libre+Caslon+Text:wght@700&display=swap">
<style>
  :root {
    --poster-red: #b71c2f;
    --poster-red-deep: #a3172a;
    --deep-red: #6a0c17;
    --paper-white: #ffffff;
    --sky-grey: #b9c1c1;
    --bridge-grey: #4a5254;
    --river-grey: #7f898a;
    --bank-grey: #363c3e;
  }
  html, body {
    margin: 0;
    padding: 0;
    overflow: hidden;
    background: #ffffff;
  }
  .poster {
    position: relative;
    width: 849px;
    height: 1200px;
    overflow: hidden;
  }
  .backdrop-photo {
    position: absolute;
    inset: 0;
    background: linear-gradient(180deg,
      #a9b1b2 0%,
      var(--sky-grey) 30%,
      #9aa3a4 44%,
      var(--bridge-grey) 50%,
      #5b6466 56%,
      var(--bridge-grey) 64%,
      var(--river-grey) 72%,
      #8d9798 84%,
      #6f797a 90%,
      var(--bank-grey) 94%,
      #2e3335 100%);
  }
  .red-panel {
    position: absolute;
    left: 50px;
    top: 53px;
    width: 747px;
    height: 1096px;
    background: linear-gradient(180deg,
      #bb1e31 0%,
      var(--poster-red) 38%,
      #a9192b 48%,
      #9e1628 58%,
      #ae1a2d 70%,
      var(--poster-red-deep) 88%,
      #9b1526 100%);
    opacity: 0.97;
  }
  .presenter {
    position: absolute;
    left: 84px;
    top: 313px;
    margin: 0;
    font-family: "Libre Caslon Text", serif;
    font-weight: 700;
    font-size: 15px;
    color: var(--paper-white);
    white-space: nowrap;
  }
  .presenter .muted,
  .credit .muted {
    color: var(--deep-red);
  }
  .title {
    margin: 0;
    font-family: "Playfair Display", serif;
    font-weight: 400;
    color: var(--paper-white);
    line-height: 1;
  }
  .title-line {
    position: absolute;
    left: 80px;
    white-space: nowrap;
  }
  .title-the {
    top: 309px;
    font-size: 222px;
    letter-spacing: 6px;
  }
  .title-main {
    top: 646px;
    font-size: 158px;
    letter-spacing: -1px;
  }
  .credit {
    position: absolute;
    right: 78px;
    top: 597px;
    margin: 0;
    font-family: "Libre Caslon Text", serif;
    font-weight: 700;
    font-size: 15px;
    color: var(--paper-white);
    white-space: nowrap;
  }
  .tagline {
    position: absolute;
    left: 82px;
    top: 800px;
    margin: 0;
    font-family: "Playfair Display", serif;
    font-weight: 400;
    font-size: 40px;
    line-height: 1;
    color: var(--paper-white);
    white-space: nowrap;
  }
</style>
</head>
<body>
  <main class="poster">
    <div class="backdrop-photo" role="img" aria-label="Black and white photograph of an arched bridge crossing a wide river beside the town, with sky above and the riverbank below"></div>
    <div class="red-panel"></div>

    <p class="presenter">MURRAYVALE THEATRE COMPANY <span class="muted">PRESENTS TO YOU</span></p>

    <h1 class="title">
      <span class="title-line title-the">THE</span>
      <span class="title-line title-main">LANTERN</span>
    </h1>

    <p class="credit"><span class="muted">WRITTEN BY</span> DELL HARROW</p>

    <p class="tagline">“a river runs through the town itself”</p>
  </main>
</body>
</html>
```